Luvra's Enchilada Special

Luvra's Restaurant is looking for a flyer design for an Enchilada Special. We wanna thank our loyal customers for preferring us , and invite new ones .
The price is gonna be $3.99
we also would like to invite people to like us on facebook .
facebook.com/luvrasrestaurant
We want the logo to be present and the Enchiladas picture too .
thank you .
Updates
Luvra's
618 N. 254
Arenal, Texas 78590
956-481-5096
THANK YOU EVERYONE FOR POSTING YOUR DESIGNS .. I WAS VERY HAPPY WITH ALL THE DESIGNS .. I WAS LOOKING FOR SOMETHING SIMPLE AND I ALREADY MADE A PICK.. I SAW SOME GREAT DESIGNS WITH ALOT OF POTENTIAL FOR OTHER PROJECTS .. ILL BE POSTING A MENU COVER BY THIS WEEK .. I HOPE YOU CAN ALL PARTICIPATE . THANK YOU AND FORGIVE ME FOR NOT BEING ABLE TO GIVE TO MUCH FEEDBACK BUT ITS BEEN ONE CRAZY WEEK . THANKS LUVRA

```html
<!DOCTYPE html>
<html lang="en">
<head>
<meta charset="utf-8">
<title>Luvra's Enchilada Special</title>
<link href="https://fonts.googleapis.com/css2?family=Montserrat:wght@700;800;900&display=swap" rel="stylesheet">
<style>
  :root {
    --green-deep: #0f6a34;
    --green-mid: #2f7a3c;
    --green-soft: #4f8a45;
    --yellow: #f7d94c;
    --white: #ffffff;
    --food-red: #c2451f;
    --food-orange: #e9a23a;
  }
  * { margin: 0; padding: 0; box-sizing: border-box; }
  html, body { width: 1200px; height: 846px; overflow: hidden; background: var(--green-mid); }
  .flyer {
    position: relative;
    width: 1200px;
    height: 846px;
    overflow: hidden;
    font-family: "Montserrat", sans-serif;
    background: radial-gradient(ellipse at 55% 60%, var(--green-soft) 0%, var(--green-mid) 55%, #256b33 100%);
  }
  .title-band { position: absolute; inset: 0; }
  .brand-oval {
    position: absolute;
    left: 18px; top: 22px;
    width: 452px; height: 362px;
    border-radius: 50%;
    background: var(--green-deep);
    border: 6px solid var(--yellow);
    display: flex; align-items: center; justify-content: center; gap: 14px;
  }
  .brand-oval .brand-dot {
    width: 34px; height: 34px; border-radius: 50%; background: var(--yellow);
  }
  .brand-oval .brand-name {
    color: var(--yellow); font-weight: 900; font-size: 70px; letter-spacing: 1px;
  }
  .headline {
    position: absolute;
    left: 478px; top: 44px;
    width: 716px;
    text-align: center;
    color: var(--yellow);
    font-weight: 800;
    font-size: 110px;
    line-height: 124px;
    white-space: nowrap;
  }
  .price {
    position: absolute;
    left: 50px; top: 404px;
    color: var(--white);
    font-weight: 900;
    line-height: 1;
  }
  .price .price-lead { display: block; font-size: 136px; letter-spacing: -3px; }
  .price .price-amount { display: block; font-size: 136px; letter-spacing: -5px; margin-top: 12px; }
  .dish-photo {
    position: absolute;
    left: 440px; top: 320px;
    width: 746px; height: 406px;
    border-radius: 50%;
    transform: rotate(-3deg);
    background: radial-gradient(ellipse at 50% 50%, var(--food-red) 0%, var(--food-orange) 35%, #a86a3c 55%, #f4f1ea 72%, var(--white) 100%);
  }
  .contact-bar {
    position: absolute;
    left: 19px; top: 733px;
    width: 1164px; height: 95px;
    background: var(--green-deep);
    border: 4px solid var(--yellow);
    display: flex; justify-content: space-between; align-items: center;
    padding: 0 56px 0 62px;
    color: var(--yellow);
    font-weight: 800;
    font-size: 26px;
    line-height: 36px;
    text-align: center;
  }
</style>
</head>
<body>
<main class="flyer">
  <svg class="title-band" width="1200" height="846" viewBox="0 0 1200 846">
    <polygon points="0,92 1200,10 1200,276 0,353" fill="#0f6a34"/>
    <line x1="0" y1="92" x2="1200" y2="10" stroke="#f7d94c" stroke-width="6"/>
    <line x1="0" y1="353" x2="1200" y2="276" stroke="#f7d94c" stroke-width="6"/>
  </svg>

  <div class="brand-oval">
    <span class="brand-dot"></span>
    <span class="brand-name">Luvra's</span>
  </div>

  <h1 class="headline">ENCHILADA<br>SPECIAL</h1>

  <p class="price">
    <span class="price-lead">Only</span>
    <span class="price-amount">$3.99</span>
  </p>

  <div class="dish-photo" role="img" aria-label="Plate of cheese-topped enchiladas in red sauce with Mexican rice and refried beans"></div>

  <footer class="contact-bar">
    <div class="contact-location">618 N. 254, Arenal, Texas 78590<br>Mon - Sun: 7:30 am - 9:00 pm</div>
    <div class="contact-reach">Phone: 956-481-5096<br>facebook.com/luvrasrestaurant</div>
  </footer>
</main>
</body>
</html>
```